Brimlow OrthoLink IT Inc. new website

i need a website for my company which is dedicated to installation and service of computer systems in Dental Offices. I would like for it to encompass a technology feel and professional look. The company deals with all aspects of technology like, Audio Visual, computer systems and networks, Cloud services like data backup, data center. We provide manage services, support and services to Dental Professionals.
Updates

Looking for a Technology font but professional look Added Wednesday, April 20, 2016

Target Market(s)

Dental, Dentist

Industry/Entity Type

Dental

Number of Pages Required

5+ page

Font styles to use
Other font styles liked:
• Futuristic or Techy

Colors
0255a3
ec1f27

Requirements
Must have
• Tabs
Nice to have
• Have no idea maybe some suggestion on your part may help
Should not have
• A professional feel but have a techy look

```html
<!DOCTYPE html>
<html lang="en">
<head>
<meta charset="utf-8">
<title>Brimlow OrthoLink IT</title>
<link href="https://fonts.googleapis.com/css2?family=Lato:wght@400;700;900&family=Open+Sans:wght@400;600;700&family=Roboto+Condensed:wght@300;400;700&display=swap" rel="stylesheet">
<style>
:root{
  --blue:#0255a3;
  --blue-dark:#034a8f;
  --ink:#1c1c1c;
  --text:#555;
  --footer:#2b2b2b;
  --footer-text:#bdbdbd;
  --white:#fff;
}
*{margin:0;padding:0;box-sizing:border-box}
html,body{width:1200px;height:2663px;overflow:hidden;background:var(--white)}
body{font-family:'Open Sans',sans-serif;color:var(--text);position:relative}
section,header,footer,.topbar{position:relative;width:1200px}
.abs{position:absolute}
svg{flex-shrink:0}

.topbar{height:43px;background:#111;color:var(--white)}
.topbar .social{left:76px;top:12px;display:flex;gap:18px}
.topbar .social span{width:18px;height:18px;border-radius:50%;background:var(--white);display:block}
.topbar .contact{right:76px;top:9px;display:flex;gap:30px;font-size:19px;align-items:center}
.topbar .contact b{font-weight:700}
.topbar svg{vertical-align:-3px;margin-right:6px}

.site-header{height:119px;background:var(--white)}
.brand{left:80px;top:34px;display:flex;align-items:center;gap:12px}
.brand-mark{width:40px;height:40px;background:var(--blue);border-radius:6px}
.brand-name{font-family:'Roboto Condensed',sans-serif;font-weight:700;font-size:28px;color:var(--blue);line-height:1.05;width:190px}
.nav{left:449px;top:35px;display:flex;align-items:center;font-family:'Roboto Condensed',sans-serif;font-size:18px;color:#555}
.nav a{color:inherit;text-decoration:none;padding:0 15px;height:43px;line-height:43px;margin-right:10px}
.nav a.active{background:var(--blue);color:var(--white);padding:0 25px;border-radius:2px}

.hero{height:490px;overflow:hidden}
.hero-photo{inset:0;background:linear-gradient(90deg,#f7f9fb 0%,#eef2f7 35%,#d9e1ea 60%,#c9d3de 100%)}
.hero h1{left:78px;top:86px;font-family:'Lato',sans-serif;font-weight:900;font-size:44px;line-height:62px;color:var(--ink)}
.hero p{left:78px;top:216px;width:420px;font-family:'Roboto Condensed',sans-serif;font-size:20px;line-height:30px;color:#222}
.btn-solid{left:78px;top:301px;width:202px;height:61px;background:var(--blue);color:var(--white);font-family:'Roboto Condensed',sans-serif;font-weight:700;font-size:25px;display:flex;align-items:center;justify-content:center;border-radius:3px}

.welcome{height:319px;text-align:center}
.welcome-photo{left:1035px;top:37px;width:135px;height:282px;background:linear-gradient(180deg,#e9eef3,#cfd9e3);border-radius:68px 68px 0 0}
.welcome h2{left:0;right:0;top:50px;font-family:'Lato',sans-serif;font-weight:400;font-size:38px;color:var(--ink);z-index:1}
.welcome h2 span{color:var(--blue)}
.welcome p{left:175px;width:850px;top:120px;font-size:14.5px;line-height:25px;color:#777;z-index:1}
.btn-outline{left:456px;top:213px;width:311px;height:52px;border:2px solid #9bb6d6;color:var(--blue);font-family:'Roboto Condensed',sans-serif;font-size:23px;display:flex;align-items:center;justify-content:center;border-radius:3px;z-index:1}

.technology{height:467px;background:radial-gradient(ellipse at 25% 30%,#1d77cf 0%,#0a5db0 40%,#0255a3 100%);color:var(--white)}
.technology h2{left:360px;top:40px;font-family:'Roboto Condensed',sans-serif;font-weight:300;font-size:52px}
.tech-photo{left:80px;top:99px;width:190px;height:368px;background:linear-gradient(180deg,#1b3d66 0%,#c99a7e 60%,#b98566 100%);border-radius:18px 18px 0 0;opacity:.85}
.tech-item{width:260px;text-align:center;top:146px}
.tech-icon{width:104px;height:104px;background:#063f7b;border-radius:4px;margin:0 auto 22px;display:flex;align-items:center;justify-content:center}
.tech-item h3{font-family:'Roboto Condensed',sans-serif;font-weight:400;font-size:25px;line-height:37px}
.tech-item p{font-family:'Roboto Condensed',sans-serif;font-size:16px;line-height:25px;color:#dfe9f5;margin-top:4px;padding:0 20px}

.services{height:261px}
.service-photo{width:208px;height:135px;top:56px;background:linear-gradient(135deg,#c9ccd2,#7f8794)}
.service-photo.two{background:linear-gradient(135deg,#eef1f4,#c8ced6)}
.service h3{font-family:'Roboto Condensed',sans-serif;font-weight:400;font-size:27px;color:var(--blue)}
.service p{font-size:15px;line-height:25px;color:#777;width:270px;margin-top:6px}

.testimonials{height:369px;background:linear-gradient(90deg,#dfe2e5,#eceef0 50%,#e1e4e6);text-align:center}
.testimonials h2{left:0;right:0;top:56px;font-family:'Roboto Condensed',sans-serif;font-weight:400;font-size:40px;color:var(--ink)}
.testimonials h2 span{color:var(--blue)}
.quote-mark{left:0;right:0;top:124px;font-family:'Lato',sans-serif;font-weight:900;font-size:84px;line-height:70px;height:50px;color:#444}
.testimonials p{left:220px;width:760px;top:185px;font-size:15.5px;line-height:25px;color:#333}
.client-name{left:0;right:0;top:284px;color:var(--blue);font-weight:700;font-size:15.5px}
.arrow{top:176px;width:62px;height:62px;border:2px solid #222;border-radius:50%;display:flex;align-items:center;justify-content:center}

.news{height:266px}
.news h2{left:0;right:0;top:40px;text-align:center;font-family:'Roboto Condensed',sans-serif;font-weight:400;font-size:40px;color:var(--ink)}
.news h2 span{color:var(--blue)}
.news-item{top:126px;display:flex;gap:14px}
.news-date{width:71px;height:82px;background:var(--blue);color:var(--white);text-align:center;font-family:'Roboto Condensed',sans-serif;padding-top:10px}
.news-date b{display:block;font-size:32px;line-height:36px}
.news-date small{font-size:16px}
.news-item p{font-size:14.5px;line-height:25px;color:#777;width:250px}
.news-item a{display:block;font-weight:700;color:#111;text-decoration:none;font-size:14px}

.site-footer{height:329px;background:var(--footer);color:var(--footer-text);font-size:15px}
.site-footer h4{font-weight:400;font-size:20px;color:var(--white);margin-bottom:14px}
.footer-col{top:30px}
.links li{list-style:none;line-height:31px;font-size:15.5px;color:#9a9a9a}
.links li::before{content:"»";margin-right:10px;color:#ddd;font-size:20px}
.links li.active{color:var(--white)}
.blog-entry{line-height:23px;width:230px;margin-bottom:28px}
.newsletter-note{width:240px;font-size:13.5px;line-height:19px;color:#ddd;margin:-6px 0 10px}
.field{width:232px;height:37px;border:1px solid #ccc;color:#ddd;padding-left:8px;line-height:35px;margin-bottom:10px;font-size:15px}
.subscribe{width:158px;height:40px;background:var(--blue);color:var(--white);text-align:center;line-height:40px;font-size:20px;margin-top:4px}
.info-line{display:flex;gap:10px;line-height:22px;margin-bottom:12px;width:240px}
.phone{font-size:21px;font-weight:700;color:var(--white)}
.socials{display:flex;gap:14px;margin-top:4px}
.socials span{width:46px;height:46px;border-radius:50%;border:2px solid var(--white)}
.socials span.filled{background:var(--white)}
.footer-rule{left:78px;right:78px;top:276px;height:1px;background:#444}
.copyright{left:0;right:0;top:290px;text-align:center;color:#ddd;font-size:15px}
.copyright b{color:var(--white)}
</style>
</head>
<body>

<div class="topbar">
  <div class="abs social"><span></span><span></span><span></span></div>
  <div class="abs contact">
    <span><svg width="20" height="16" viewBox="0 0 20 16"><rect x="1" y="1" width="18" height="14" fill="none" stroke="#fff" stroke-width="2"/><path d="M1 1l9 8 9-8" fill="none" stroke="#fff" stroke-width="2"/></svg>info@brimlowortholink.com</span>
    <b><svg width="20" height="20" viewBox="0 0 20 20"><path d="M4 1l4 4-2 3c1 3 3 5 6 6l3-2 4 4-3 3C9 19 1 11 1 4z" fill="#fff"/></svg>123 456 7890</b>
  </div>
</div>

<header class="site-header">
  <div class="abs brand">
    <span class="brand-mark"></span>
    <span class="brand-name">Brimlow OrthoLink IT</span>
  </div>
  <nav class="abs nav">
    <a class="active">HOME</a><a>ABOUT</a><a>SERVICES</a><a>SUPPORT</a><a>CLIENT</a><a>BLOG</a><a>CONTACT</a>
  </nav>
</header>

<section class="hero">
  <div class="abs hero-photo" role="img" aria-label="Bright dental treatment room with an X-ray display screen"></div>
  <h1 class="abs">TECHNOLOGY FOR<br>BEST PRACTICE</h1>
  <p class="abs">f you view technology as an expense rather than an investment, you haven't worked with us.</p>
  <div class="abs btn-solid">CONTACT US</div>
</section>

<section class="welcome">
  <div class="abs welcome-photo" role="img" aria-label="Dental professional in a white coat holding a tablet"></div>
  <h2 class="abs">Welcome to <span>Brimlow OrthoLink IT</span></h2>
  <p class="abs">Lorem Ipsum is simply dummy text of the printing and typesetting industry. Lorem Ipsum has been the industry's standard dummy text ever since the 1500s, when an unknown printer took a galley of type and scrambled it to make a type specimen book.</p>
  <div class="abs btn-outline">GET OUR CUSTOM SUPPORT</div>
</section>

<section class="technology">
  <h2 class="abs">Our Technology</h2>
  <div class="abs tech-photo" role="img" aria-label="Hand pointing up at a floating screen icon"></div>
  <div class="abs tech-item" style="left:300px">
    <div class="tech-icon"><svg width="54" height="48" viewBox="0 0 54 48" fill="none" stroke="#fff" stroke-width="3"><rect x="3" y="3" width="48" height="32" rx="2"/><path d="M20 44h14M27 35v9"/><path d="M22 13l12 6-12 6z" fill="#fff"/></svg></div>
    <h3>Audio Visual</h3>
    <p>Lorem Ipsum is simply dummy text of the printing and type...</p>
  </div>
  <div class="abs tech-item" style="left:592px">
    <div class="tech-icon"><svg width="58" height="50" viewBox="0 0 58 50" fill="none" stroke="#fff" stroke-width="3"><rect x="3" y="12" width="24" height="18"/><path d="M10 38h10M15 30v8M27 21h10M37 6v38M37 6h8M37 25h8M37 44h8"/><rect x="45" y="2" width="10" height="8"/><rect x="45" y="21" width="10" height="8"/><rect x="45" y="40" width="10" height="8"/></svg></div>
    <h3>Computer Systems<br>and Networks</h3>
    <p>Lorem Ipsum is simply dummy text of the printing and type...</p>
  </div>
  <div class="abs tech-item" style="left:867px">
    <div class="tech-icon"><svg width="60" height="48" viewBox="0 0 60 48" fill="none" stroke="#fff" stroke-width="3"><path d="M14 36C6 36 3 30 3 26c0-6 5-10 10-9 2-8 9-13 17-12 8 1 13 7 13 14 6 0 10 4 10 9"/><ellipse cx="44" cy="32" rx="11" ry="4"/><path d="M33 32v10c0 2 5 4 11 4s11-2 11-4V32"/></svg></div>
    <h3>Cloud Services of<br>Data Backup</h3>
    <p>Lorem Ipsum is simply dummy text of the printing and type...</p>
  </div>
</section>

<section class="services">
  <div class="abs service-photo" style="left:78px" role="img" aria-label="Business team reviewing documents at a desk"></div>
  <div class="abs service" style="left:302px;top:50px">
    <h3>Manage services</h3>
    <p>Lorem Ipsum is simply dummy text of the printing and typesetting industry. Lorem Ipsum has been the industry.</p>
  </div>
  <div class="abs service-photo two" style="left:637px" role="img" aria-label="Support team wearing headsets"></div>
  <div class="abs service" style="left:862px;top:50px">
    <h3>Support</h3>
    <p>Lorem Ipsum is simply dummy text of the printing and typesetting industry. Lorem Ipsum has been the industry.</p>
  </div>
</section>

<section class="testimonials" role="img" aria-label="Faded dental clinic interior background">
  <h2 class="abs">What Our <span>Client Say</span></h2>
  <div class="abs quote-mark">&ldquo;</div>
  <p class="abs">Lorem Ipsum is simply dummy text of the printing and typesetting industry. Lorem Ipsum has been the industry's standard dummy text ever since the 1500.Lorem Ipsum is simply dummy text of the printing and typesetting industry.</p>
  <div class="abs client-name">- Client Name</div>
  <div class="abs arrow" style="left:78px"><svg width="16" height="28" viewBox="0 0 16 28"><path d="M14 2L3 14l11 12" fill="none" stroke="#222" stroke-width="2"/></svg></div>
  <div class="abs arrow" style="left:1056px"><svg width="16" height="28" viewBox="0 0 16 28"><path d="M2 2l11 12L2 26" fill="none" stroke="#222" stroke-width="2"/></svg></div>
</section>

<section class="news">
  <h2 class="abs">LATEST <span>NEWS</span></h2>
  <div class="abs news-item" style="left:78px">
    <div class="news-date"><b>21</b><small>Apr</small></div>
    <div><p>Lorem Ipsum is simply dummy text of the print &amp; typesetting industry.</p><a>READ MORE</a></div>
  </div>
  <div class="abs news-item" style="left:435px">
    <div class="news-date"><b>20</b><small>Apr</small></div>
    <div><p>Lorem Ipsum is simply dummy text of the print &amp; typesetting industry.</p><a>READ MORE</a></div>
  </div>
  <div class="abs news-item" style="left:800px">
    <div class="news-date"><b>19</b><small>Apr</small></div>
    <div><p>Lorem Ipsum is simply dummy text of the print &amp; typesetting industry.</p><a>READ MORE</a></div>
  </div>
</section>

<footer class="site-footer">
  <div class="abs footer-col" style="left:80px">
    <h4>Useful Links</h4>
    <ul class="links">
      <li class="active">Home</li><li>About</li><li>Services</li><li>Support</li><li>News</li><li>Contact</li>
    </ul>
  </div>
  <div class="abs footer-col" style="left:351px">
    <h4>Recent Blog</h4>
    <div class="blog-entry">Lorem Ipsum is simply dummy text of the printing.<br>21 April 2016</div>
    <div class="blog-entry">Lorem Ipsum is simply dummy text of the printing.<br>21 April 2016</div>
  </div>
  <div class="abs footer-col" style="left:621px">
    <h4>Newsletter</h4>
    <div class="newsletter-note">Subscribe to stay on Brimlow OrthoLink IT.</div>
    <div class="field">Enter Name</div>
    <div class="field">Enter Email</div>
    <div class="subscribe">SUBSCRIBE</div>
  </div>
  <div class="abs footer-col" style="left:891px">
    <h4>Contact Info</h4>
    <div class="info-line"><svg width="16" height="22" viewBox="0 0 16 22"><path d="M8 1C4 1 1 4 1 8c0 5 7 13 7 13s7-8 7-13c0-4-3-7-7-7z" fill="#fff"/><circle cx="8" cy="8" r="2.5" fill="#2b2b2b"/></svg><span>Lorem Ipsum is simply dummy text of the printing.</span></div>
    <div class="info-line phone"><svg width="20" height="20" viewBox="0 0 20 20" style="margin-top:2px"><path d="M4 1l4 4-2 3c1 3 3 5 6 6l3-2 4 4-3 3C9 19 1 11 1 4z" fill="#fff"/></svg>123 456 7890</div>
    <div class="info-line"><svg width="20" height="16" viewBox="0 0 20 16" style="margin-top:3px"><rect x="1" y="1" width="18" height="14" fill="none" stroke="#fff" stroke-width="2"/><path d="M1 1l9 8 9-8" fill="none" stroke="#fff" stroke-width="2"/></svg>info@brimlowortholink.com</div>
    <div class="socials"><span class="filled"></span><span></span><span></span></div>
  </div>
  <div class="abs footer-rule"></div>
  <div class="abs copyright">© <b>BRIMLOW ORTHOLINK IT</b> - 2016. All Rights Reserved.</div>
</footer>

</body>
</html>
```